Alaska Law Firm Needs a Sticker Design

We need a design for stickers to put on already-printed brochures. We mail the brochures to potential clients so they can learn more about accident-induced injuries, insurance claims, legal representation, and our own law firm.

One of our lawyers wrote a book that provides a helpful overview of personal injury claims. We are offering this book for free to anyone who calls and requests it. Therefore, the sticker design should include one of the following phrases, or something very similar:
a) "Still have questions? Call and request our book-- for free!"
b) "Still have questions about auto accident claims? Call and request our book today."
c) "Still have questions about filing a claim? Call and request a free copy of our book."
d) "Still have questions? Call us today to request a free copy of our book, Clear Lanes Ahead."
e) "To learn more about automobile accidents and insurance, call today and request a free copy of our book."

The sticker should be approximately 3"x3" and may be a circle, square, rectangle, or ellipsis. The sticker will be placed on the back of the folder, which is light blue. We would like the sticker to match the color scheme of our website and the folder.

I will upload an image of the book cover as soon as I obtain it.

Law Firm

Font styles to use
Serif
Sans Serif

Requirements
Should not have
• Bright colors that aren't already used in the folder design. e.g. no bright orange, pink, chartreuse, turquoise, yellow, red.

```html
<!DOCTYPE html>
<html lang="en">
<head>
<meta charset="utf-8">
<title>Still Have Questions? Sticker</title>
<link rel="stylesheet" href="https://fonts.googleapis.com/css2?family=Rye&family=Stardos+Stencil:wght@700&family=Kurale&family=Andika:wght@700&display=swap">
<style>
  :root {
    --navy: #1f2f8f;
    --navy-deep: #18246e;
    --ink: #1e1e1e;
    --paper: #ffffff;
    --backdrop: #ececec;
    --accent-blue: #1f33a0;
  }
  * { margin: 0; padding: 0; box-sizing: border-box; }
  html, body {
    width: 1200px; height: 1200px; overflow: hidden;
    background: var(--backdrop);
  }
  .sticker {
    position: absolute; left: 95px; top: 164px;
    width: 1010px; height: 872px;
    background: var(--paper);
    border: 20px solid var(--navy);
    border-radius: 120px;
    overflow: hidden;
  }
  .panel {
    position: absolute; left: 26px; width: 918px;
    border: 4px solid var(--ink);
  }
  .panel--top {
    top: 26px; height: 198px;
    border-radius: 95px 95px 0 0;
    display: flex; align-items: center; justify-content: center;
  }
  .panel--bottom {
    top: 420px; height: 386px;
    border-radius: 0 0 100px 100px;
    text-align: center;
  }
  .headline-lead {
    font-family: "Stardos Stencil", serif;
    font-weight: 700; font-size: 100px; letter-spacing: 3px;
    color: var(--ink); line-height: 1;
  }
  .band {
    position: absolute; left: 0; right: 0; top: 224px; height: 185px;
    background: linear-gradient(var(--navy), var(--navy-deep));
    display: flex; align-items: center; justify-content: center;
  }
  .headline-main {
    font-family: "Rye", serif;
    font-size: 122px; color: var(--paper); line-height: 1;
    text-shadow: 3px 4px 4px rgba(0,0,0,0.45);
    letter-spacing: 1px;
  }
  .offer-line {
    margin-top: 26px;
    font-family: "Kurale", serif;
    font-size: 52px; color: var(--ink); line-height: 1.1;
  }
  .offer-free {
    font-family: "Andika", sans-serif; font-weight: 700;
    color: var(--accent-blue); line-height: 0.95;
  }
  .offer-free__for {
    display: flex; align-items: center; justify-content: center; gap: 34px;
    font-size: 158px; margin-top: 6px;
  }
  .offer-free__free { font-size: 106px; margin-top: -6px; }
  .spark { width: 56px; height: 56px; }
</style>
</head>
<body>
  <div class="sticker">
    <div class="panel panel--top">
      <p class="headline-lead">STILL HAVE</p>
    </div>
    <div class="band">
      <p class="headline-main">QUESTIONS?</p>
    </div>
    <div class="panel panel--bottom">
      <p class="offer-line">Call and request our book</p>
      <div class="offer-free">
        <div class="offer-free__for">
          <svg class="spark" viewBox="-10 -10 20 20" aria-hidden="true">
            <g stroke="var(--accent-blue)" stroke-width="2.2" stroke-linecap="round">
              <line x1="0" y1="-9" x2="0" y2="9"/><line x1="-9" y1="0" x2="9" y2="0"/>
              <line x1="-6.4" y1="-6.4" x2="6.4" y2="6.4"/><line x1="-6.4" y1="6.4" x2="6.4" y2="-6.4"/>
            </g>
          </svg>
          <span>FOR</span>
          <svg class="spark" viewBox="-10 -10 20 20" aria-hidden="true">
            <g stroke="var(--accent-blue)" stroke-width="2.2" stroke-linecap="round">
              <line x1="0" y1="-9" x2="0" y2="9"/><line x1="-9" y1="0" x2="9" y2="0"/>
              <line x1="-6.4" y1="-6.4" x2="6.4" y2="6.4"/><line x1="-6.4" y1="6.4" x2="6.4" y2="-6.4"/>
            </g>
          </svg>
        </div>
        <div class="offer-free__free">FREE!</div>
      </div>
    </div>
  </div>
</body>
</html>
```